Business Card Design for Flood Rescue 360 - Property Restoration Professionals

I need a business card designed for Flood Rescue 360. We are a full-service property restoration solution. Providing water, fire, smoke & storm restoration as well as mold remediation and full remodel or reconstruction to homes and businesses across Dallas-Fort Worth, TX.
Target Market(s)
home and business owners with insurance covered property damage from water, fire or storm related damage
Industry/Entity Type
property restoration
Contact Information for Business Card
Marcus Pelley General Manager Cell: 214-555-0193 Office: 469-555-0148 email: Marcus@FloodRescue360.example services: Water, Fire, Mold, Reconstruction Tagline: Urgency for Your Water Emergency!
Look and feel
Each slider illustrates characteristics of the customer's brand and the style your logo design should communicate.

```html
<!DOCTYPE html>
<html lang="en">
<head>
<meta charset="utf-8">
<title>Flood Rescue 360 – Business Card</title>
<link rel="stylesheet" href="https://fonts.googleapis.com/css2?family=Lato:wght@400;700;900&display=swap">
<style>
  :root {
    --brand-blue: #00b3e6;
    --ink-grey: #555a60;
    --card-white: #ffffff;
    --faint-grey: #eeeeef;
    --backdrop: #2b2d31;
  }
  * { margin: 0; padding: 0; box-sizing: border-box; }
  html, body { width: 1200px; height: 952px; overflow: hidden; }
  body {
    background: var(--backdrop);
    font-family: "Lato", sans-serif;
    display: flex;
    align-items: center;
    justify-content: center;
    gap: 40px;
  }
  .card {
    position: relative;
    width: 560px;
    height: 320px;
    overflow: hidden;
    box-shadow: 0 18px 40px rgba(0,0,0,0.45);
  }
  /* Front */
  .card-front {
    background: var(--brand-blue);
    display: flex;
    align-items: center;
    justify-content: center;
  }
  .front-name {
    color: var(--card-white);
    font-weight: 900;
    font-size: 40px;
    letter-spacing: 1px;
    text-transform: uppercase;
    white-space: nowrap;
  }
  /* Back */
  .card-back { background: var(--card-white); }
  .back-name {
    position: absolute;
    right: 22px; bottom: 14px;
    color: var(--faint-grey);
    font-weight: 900;
    font-size: 22px;
    letter-spacing: 1px;
    text-transform: uppercase;
    white-space: nowrap;
  }
  .person { position: absolute; left: 150px; top: 30px; }
  .person-name {
    color: var(--brand-blue);
    font-size: 30px;
    font-weight: 400;
    letter-spacing: 1px;
    text-transform: uppercase;
  }
  .person-name strong { font-weight: 900; }
  .person-title { color: var(--ink-grey); font-size: 16px; margin-top: -2px; }
  .contacts { position: absolute; left: 130px; top: 100px; list-style: none; }
  .contacts li {
    display: flex; align-items: center; gap: 8px;
    color: var(--ink-grey); font-size: 14px; margin-bottom: 4px;
  }
  .contacts svg { width: 15px; height: 15px; flex: none; }
  .band { position: absolute; left: 0; top: 170px; width: 360px; height: 100px; }
  .band-text {
    position: absolute; left: 22px; top: 182px;
    color: var(--card-white);
  }
  .tagline { font-weight: 900; font-size: 17px; line-height: 1.15; text-transform: uppercase; }
  .services { font-size: 13px; margin-top: 6px; line-height: 1.35; }
</style>
</head>
<body>
  <section class="card card-front" aria-label="Card front">
    <p class="front-name">Flood Rescue 360</p>
  </section>

  <section class="card card-back" aria-label="Card back">
    <p class="back-name" aria-hidden="true">Flood Rescue 360</p>

    <div class="person">
      <h1 class="person-name">Marcus <strong>Pelley</strong></h1>
      <p class="person-title">General Manager</p>
    </div>

    <ul class="contacts">
      <li>
        <svg viewBox="0 0 16 16"><rect width="16" height="16" rx="3" fill="#555a60"/><path d="M5 3.5l2 2-1 1.2c.6 1.3 1.5 2.2 2.8 2.8l1.2-1 2 2-1.2 1.5C7.6 11.8 4.2 8.4 3.5 5z" fill="#fff"/></svg>
        <span>214-555-0193</span>
      </li>
      <li>
        <svg viewBox="0 0 16 16"><rect width="16" height="16" rx="3" fill="#555a60"/><rect x="4" y="6" width="8" height="6" rx="1" fill="#fff"/><path d="M3 6.5c1-2.5 9-2.5 10 0" stroke="#fff" stroke-width="1.5" fill="none"/></svg>
        <span>469-555-0148</span>
      </li>
      <li>
        <svg viewBox="0 0 16 16"><rect width="16" height="16" rx="3" fill="#555a60"/><rect x="3" y="4.5" width="10" height="7" fill="#fff"/><path d="M3 4.5l5 4 5-4" stroke="#555a60" stroke-width="1" fill="none"/></svg>
        <span>Marcus@FloodRescue360.example</span>
      </li>
    </ul>

    <svg class="band" viewBox="0 0 360 100" aria-hidden="true">
      <polygon points="0,0 330,0 318,14 340,14 310,100 0,100" fill="var(--brand-blue)"/>
    </svg>
    <div class="band-text">
      <p class="tagline">Urgency for your<br>water emergency!</p>
      <p class="services">• Water &nbsp;• Fire<br>• Mold &nbsp;• Reconstruction</p>
    </div>
  </section>
</body>
</html>
```